Design a Travel and Tourism website

We would like a freelancer to design a website that is essentially easy to use and navigate database providing local information for Travelers about destination countries.

We proposed website would discuss different rates, fees, visa requirement, resort locations, cheap flights, etc. This website should be elegant and modern. Our business name is rovanix.
Some reference websites are zemplorift.ca, brindlefoxhaven.com,
There should be a forum in the website where travell\ers discuss about their first hand tranvel experience to such destinations.

Tourism

```html
<!DOCTYPE html>
<html lang="en">
<head>
<meta charset="utf-8">
<title>rovanix – traveller forum</title>
<link rel="stylesheet" href="https://fonts.googleapis.com/css2?family=Figtree:wght@300;400;600;700&display=swap">
<style>
  :root {
    --bg: #ffffff;
    --ink: #4b5262;
    --ink-soft: #5f6b82;
    --muted: #a39e95;
    --rule: #dcdde1;
    --chevron: #c9ccd2;
    --avatar-ring: #eceef1;
    --avatar-jane: linear-gradient(160deg, #c98a55 0%, #e7b89a 50%, #8a5a34 100%);
    --avatar-john: linear-gradient(160deg, #8fa3b3 0%, #c9a58c 55%, #6b5a4e 100%);
  }
  * { box-sizing: border-box; margin: 0; padding: 0; }
  html, body { width: 1200px; height: 1200px; overflow: hidden; }
  body {
    background: var(--bg);
    font-family: "Figtree", sans-serif;
    color: var(--ink-soft);
    position: relative;
  }

  .brand {
    position: absolute;
    left: 80px;
    top: 66px;
    display: flex;
    align-items: center;
    gap: 16px;
  }
  .brand-dot {
    width: 40px; height: 40px;
    border-radius: 50%;
    border: 4px solid var(--ink);
  }
  .brand-name {
    font-size: 46px;
    font-weight: 300;
    letter-spacing: 1px;
    color: var(--ink);
    text-transform: uppercase;
  }

  .app-screen {
    position: absolute;
    left: 320px;
    top: 170px;
    width: 560px;
    height: 1030px;
    background: var(--bg);
    border-left: 1px solid var(--rule);
    border-right: 1px solid var(--rule);
    overflow: hidden;
  }

  .app-header {
    height: 148px;
    border-bottom: 1px solid var(--rule);
    display: flex;
    align-items: center;
    padding: 0 52px 0 44px;
  }
  .app-brand {
    font-size: 22px;
    font-weight: 600;
    color: var(--ink);
  }
  .lang-switch {
    margin-left: 28px;
    font-size: 17px;
    font-weight: 600;
    color: var(--ink);
    display: flex;
    align-items: center;
    gap: 6px;
  }
  .menu-toggle { margin-left: auto; }

  .post {
    position: relative;
    text-align: center;
    padding: 44px 0 72px;
    border-bottom: 1px solid var(--rule);
  }
  .avatar {
    border-radius: 50%;
    border: 5px solid var(--avatar-ring);
  }
  .avatar--jane {
    width: 112px; height: 112px;
    margin: 0 auto;
    background: var(--avatar-jane);
  }
  .post-author {
    margin-top: 30px;
    font-size: 21px;
    font-weight: 700;
    color: var(--ink-soft);
  }
  .post-time {
    font-size: 18px;
    font-weight: 400;
    margin-top: 2px;
  }
  .post-place {
    margin-top: 22px;
    font-size: 17px;
    letter-spacing: 3px;
    color: var(--muted);
    text-transform: uppercase;
  }
  .post-body {
    margin: 28px auto 0;
    width: 320px;
    font-size: 19px;
    line-height: 25px;
    font-weight: 400;
  }
  .post-nav {
    position: absolute;
    top: 305px;
  }
  .post-nav--prev { left: 44px; }
  .post-nav--next { right: 44px; }
  .comment-button {
    display: block;
    margin: 42px auto 0;
    width: 278px;
    height: 51px;
    border: 1px solid var(--ink);
    border-radius: 10px;
    background: transparent;
    font-family: "Figtree", sans-serif;
    font-size: 22px;
    font-weight: 700;
    color: var(--ink);
  }

  .reply { padding: 36px 52px; }
  .reply-head {
    display: flex;
    align-items: center;
    gap: 26px;
  }
  .avatar--john {
    width: 112px; height: 112px;
    background: var(--avatar-john);
    flex: none;
  }
  .reply-author {
    font-size: 21px;
    font-weight: 700;
  }
  .reply-time {
    font-size: 18px;
  }
  .reply-body {
    margin-top: 22px;
    margin-left: 14px;
    font-size: 19px;
  }
</style>
</head>
<body>

  <header class="brand">
    <span class="brand-dot"></span>
    <span class="brand-name">rovanix</span>
  </header>

  <main class="app-screen">
    <div class="app-header">
      <span class="app-brand">rovanix</span>
      <span class="lang-switch">FR
        <svg width="18" height="12" viewBox="0 0 18 12"><path d="M2 2 L9 9 L16 2" fill="none" stroke="#4b5262" stroke-width="2.4"/></svg>
      </span>
      <svg class="menu-toggle" width="58" height="34" viewBox="0 0 58 34">
        <g stroke="#4b5262" stroke-width="2"><line x1="0" y1="1" x2="58" y2="1"/><line x1="0" y1="17" x2="58" y2="17"/><line x1="0" y1="33" x2="58" y2="33"/></g>
      </svg>
    </div>

    <article class="post">
      <div class="avatar avatar--jane" role="img" aria-label="Profile photo of janedoe"></div>
      <p class="post-author">by janedoe</p>
      <p class="post-time">posted 5 days ago</p>
      <p class="post-place">Scotland</p>
      <p class="post-body">Lorem ipsum dolor sit amet, consectetur adipisicing elit, sed do eiusmod tempor incididunt ut labore et dolore magna aliqua.</p>
      <svg class="post-nav post-nav--prev" width="30" height="56" viewBox="0 0 30 56"><path d="M28 1 L2 28 L28 55" fill="none" stroke="#c9ccd2" stroke-width="1.5"/></svg>
      <svg class="post-nav post-nav--next" width="30" height="56" viewBox="0 0 30 56"><path d="M2 1 L28 28 L2 55" fill="none" stroke="#c9ccd2" stroke-width="1.5"/></svg>
      <button class="comment-button">comment</button>
    </article>

    <section class="reply">
      <div class="reply-head">
        <div class="avatar avatar--john" role="img" aria-label="Profile photo of johndoe"></div>
        <div>
          <p class="reply-author">by johndoe</p>
          <p class="reply-time">posted 45mins ago</p>
        </div>
      </div>
      <p class="reply-body">Tempor incididunt ut labore et dolore!</p>
    </section>
  </main>

</body>
</html>
```